Spring Detox sale graphics for social media

You MUST read the Brief in the WORD document and follow the instructions there. I want to create 10 social media graphics (new Instagram size 4:5 (1080 x 1350 pixels) focusing on our Mother’s Day Spring Detox Sale graphics, using any of the pics attached. Use the attached pics, NO RANDOM STOCK PHOTOGRAPHY. For the color scheme of the graphics, they should all be complementary to the product colors or feel like Spring time.

Target Market(s)

primarily women

Requirements
Must have
• the photos and text attached

```html
<!DOCTYPE html>
<html lang="en">
<head>
<meta charset="utf-8">
<title>Mother's Day Spring Detox Sale – Social Set</title>
<link rel="stylesheet" href="https://fonts.googleapis.com/css2?family=Oswald:wght@300;500;600;700&family=Poppins:wght@600;700&family=Archivo+Black&display=swap">
<style>
  :root{
    --canvas:#1e1e1e;
    --red:#c0202a;
    --ink:#222226;
    --white:#ffffff;
    --panel:#ececee;
    --lower:#e4e4e7;
    --pink:#fcdada;
    --blush:#f7e3ee;
    --lavender:#e9e9f8;
    --band:linear-gradient(90deg,#4f6bf5 0%,#b16fdc 30%,#2e4a48 62%,#f2453a 100%);
    --photo-person:linear-gradient(180deg,#5e4638 0%,#8d7565 35%,#e6e1dc 70%,#cfc9c4 100%);
    --photo-products:linear-gradient(180deg,#f4f4f6 0%,#e9e6ec 60%,#ded9e2 100%);
  }
  *{margin:0;padding:0;box-sizing:border-box}
  html,body{width:1200px;height:3401px;overflow:hidden;background:var(--canvas)}
  .board{position:relative;width:1200px;height:3401px}
  .tile{position:absolute;width:460px;height:574px;background:var(--white);overflow:hidden}
  .col-a{left:131px}.col-b{left:611px}
  .row-1{top:232px}.row-2{top:820px}.row-3{top:1410px}.row-4{top:2001px}.row-5{top:2594px}
  .half{position:absolute;top:0;bottom:0;left:50%;right:0}
  .half.grey{background:var(--panel)}
  .half.pink{background:linear-gradient(90deg,var(--blush),var(--pink))}
  .half.lav{background:var(--lavender)}
  .photo{position:absolute;border-radius:2px}
  .photo.person{background:var(--photo-person)}
  .photo.products{background:var(--photo-products);border-radius:10px}
  .t{position:absolute;line-height:.92;white-space:nowrap;font-family:'Oswald',sans-serif}
  .red{color:var(--red)}.ink{color:var(--ink)}
  .bold{font-weight:700}.semi{font-weight:600}.light{font-weight:300}
  .pct{font-family:'Oswald',sans-serif;font-weight:700;color:var(--red);position:absolute;line-height:.85;white-space:nowrap}
  .pct small{font-size:.42em;display:inline-block;vertical-align:top;line-height:.9}
  .wide{font-family:'Archivo Black',sans-serif}
  .band{position:absolute;left:0;right:0;top:457px;height:66px;background:var(--band);color:var(--white);
        font-family:'Poppins',sans-serif;font-weight:700;display:flex;align-items:center;justify-content:center;font-size:38px;letter-spacing:.5px;z-index:2}
  .band.xs{font-size:23px}
  .lower{position:absolute;left:0;right:0;top:523px;bottom:0;background:var(--lower)}
  .lower.pink{background:linear-gradient(90deg,var(--white) 50%,var(--pink) 50%)}
  .lower.lav{background:linear-gradient(90deg,var(--white) 50%,var(--lavender) 50%)}
  .rot{position:absolute;transform-origin:left top;transform:rotate(-90deg)}
  .bar{position:absolute;background:#1c1c1c;color:#fff;font-family:'Oswald',sans-serif;font-weight:300;font-size:34px;display:flex;align-items:center;justify-content:center}
</style>
</head>
<body>
<main class="board">

  <!-- 1 -->
  <section class="tile col-a row-1">
    <div class="photo person" style="left:230px;top:0;width:230px;height:457px" role="img" aria-label="Smiling woman in white sweater with the supplement bottles"></div>
    <div class="t red semi" style="left:30px;top:108px;font-size:60px">Mother’s</div>
    <div class="t red semi" style="left:30px;top:172px;font-size:60px">Day</div>
    <div class="t ink light" style="left:30px;top:237px;font-size:60px">SPRING</div>
    <div class="t ink light" style="left:30px;top:302px;font-size:60px">DETOX</div>
    <div class="t ink bold" style="left:30px;top:365px;font-size:60px">SALE</div>
    <div class="band">25% Off Everything!</div>
    <div class="lower"></div>
  </section>

  <!-- 2 -->
  <section class="tile col-b row-1">
    <div class="photo person" style="left:230px;top:0;width:230px;height:457px" role="img" aria-label="Smiling woman in white sweater with the supplement bottles"></div>
    <div class="pct" style="left:24px;top:68px;font-size:112px">25<small>%<br>OFF</small></div>
    <div class="t ink semi" style="left:24px;top:182px;font-size:44px">MOTHER’S</div>
    <div class="t ink semi" style="left:24px;top:234px;font-size:44px">DAY</div>
    <div class="t red" style="left:24px;top:284px;font-size:54px;font-weight:500">Spring</div>
    <div class="t red" style="left:24px;top:342px;font-size:54px;font-weight:500">Detox</div>
    <div class="band">Sale</div>
    <div class="lower"></div>
  </section>

  <!-- 3 -->
  <section class="tile col-a row-2">
    <div class="half grey"></div>
    <div class="pct" style="left:192px;top:32px;font-size:128px">25<small>%<br>OFF</small></div>
    <div class="t ink semi" style="left:194px;top:160px;font-size:30px;letter-spacing:-.3px">ALL SUPPLEMENTS</div>
    <div class="photo products" style="left:95px;top:215px;width:270px;height:150px" role="img" aria-label="Four supplement bottles in a row"></div>
    <div class="t red" style="left:45px;top:378px;font-size:66px;font-weight:500">Spring Detox</div>
    <div class="band">Sale Now!</div>
    <div class="lower"></div>
  </section>

  <!-- 4 -->
  <section class="tile col-b row-2">
    <div class="half pink"></div>
    <div class="t red bold" style="left:48px;top:28px;font-size:86px">25%</div>
    <div class="t red bold" style="left:48px;top:106px;font-size:108px">OFF</div>
    <div class="t ink" style="left:244px;top:98px;font-size:48px;font-weight:500">Spring</div>
    <div class="t ink" style="left:244px;top:152px;font-size:48px;font-weight:500">Detox</div>
    <div class="rot t red bold" style="left:378px;top:205px;font-size:72px">SALE</div>
    <div class="photo products" style="left:55px;top:228px;width:390px;height:222px" role="img" aria-label="Four supplement bottles grouped together"></div>
    <div class="band xs">Spring Reset. Summer Ready</div>
    <div class="lower pink"></div>
  </section>

  <!-- 5 -->
  <section class="tile col-a row-3">
    <div class="half pink"></div>
    <div class="photo products" style="left:20px;top:62px;width:205px;height:180px" role="img" aria-label="Two supplement bottles"></div>
    <div class="pct" style="left:250px;top:84px;font-size:112px">25<small>%<br>OFF</small></div>
    <div class="t ink semi" style="left:250px;top:196px;font-size:36px">EVERYTHING</div>
    <div class="photo products" style="left:240px;top:244px;width:205px;height:180px" role="img" aria-label="Two supplement bottles"></div>
    <div class="t ink semi" style="left:22px;top:282px;font-size:54px">Mother’s</div>
    <div class="t red bold" style="left:22px;top:340px;font-size:108px">DAY</div>
    <div class="band">Spring Detox Sale</div>
    <div class="lower pink"></div>
  </section>

  <!-- 6 -->
  <section class="tile col-b row-3">
    <div class="photo person" style="left:0;top:0;width:215px;height:457px" role="img" aria-label="Smiling woman in white sweater with the supplement bottles"></div>
    <div class="pct" style="left:236px;top:32px;font-size:116px">25<small>%<br>OFF</small></div>
    <div class="t ink semi" style="left:270px;top:160px;font-size:44px">MOTHER’S</div>
    <div class="t red bold" style="left:285px;top:212px;font-size:100px">DAY</div>
    <div class="t ink semi" style="left:316px;top:310px;font-size:62px">SALE</div>
    <div class="band">Feel Amazing Again!</div>
    <div class="lower"></div>
  </section>

  <!-- 7 -->
  <section class="tile col-a row-4">
    <div class="photo person" style="left:200px;top:0;width:260px;height:455px" role="img" aria-label="Smiling woman in white sweater with the supplement bottles"></div>
    <div class="pct" style="left:22px;top:50px;font-size:116px">25<small>%<br>OFF</small></div>
    <div class="t ink semi" style="left:22px;top:184px;font-size:30px">MOTHER’S DAY</div>
    <div class="t red bold" style="left:22px;top:222px;font-size:92px">SALE</div>
    <div class="band">Refresh Your Body</div>
    <div class="lower"></div>
  </section>

  <!-- 8 -->
  <section class="tile col-b row-4">
    <div class="half lav"></div>
    <div class="pct" style="left:38px;top:40px;font-size:176px">25<small>%<br>OFF</small></div>
    <div class="t ink semi" style="left:38px;top:222px;font-size:52px">SPRING DETOX</div>
    <div class="t red bold" style="left:38px;top:284px;font-size:148px">SALE</div>
    <div class="rot t ink bold" style="left:368px;top:445px;font-size:52px">SPRING CLEANSE.</div>
    <div class="band">SUMMER GLOW</div>
    <div class="lower lav"></div>
  </section>

  <!-- 9 -->
  <section class="tile col-a row-5">
    <div class="half pink" style="left:48%"></div>
    <div class="photo products" style="left:35px;top:20px;width:390px;height:230px" role="img" aria-label="Four supplement bottles grouped together"></div>
    <div class="t red wide" style="left:32px;top:262px;font-size:66px">25%</div>
    <div class="t ink wide" style="left:32px;top:324px;font-size:58px">OFF</div>
    <div class="t red semi" style="left:238px;top:262px;font-size:52px">Mother’s</div>
    <div class="t semi" style="left:238px;top:322px;font-size:52px"><span class="red">Day</span> <span class="ink">SALE</span></div>
    <div class="bar" style="left:30px;top:400px;width:396px;height:42px">Detox This Spring.</div>
    <div class="band">Shine This Summer</div>
    <div class="lower pink" style="background:linear-gradient(90deg,var(--white) 48%,var(--pink) 48%)"></div>
  </section>

  <!-- 10 -->
  <section class="tile col-b row-5">
    <div class="half pink"></div>
    <div class="t red wide" style="left:32px;top:26px;font-size:72px">25%</div>
    <div class="t ink wide" style="left:32px;top:94px;font-size:60px">OFF</div>
    <div class="t red semi" style="left:250px;top:72px;font-size:52px">Mother’s</div>
    <div class="t semi" style="left:250px;top:132px;font-size:52px"><span class="red">Day</span> <span class="ink">SALE</span></div>
    <div class="photo products" style="left:30px;top:200px;width:410px;height:242px" role="img" aria-label="Four supplement bottles staggered in a row"></div>
    <div class="band xs">Spring Detox for a Summer Body</div>
    <div class="lower pink"></div>
  </section>

</main>
</body>
</html>
```